Business Cards for a law firm

Business cards for our law firm. Use our silhoette logo and OAK PARTNERS - check our website (www.oakpartners.example)

Contact Information for Business Card

our silhouette logo, OAK PARTNERS, 800-555-0147, Dorian Pemberton, dorian@oakpartners.example

Requirements
Must have
• our silhouette logo, OAK PARTNERS, 800-555-0147, Dorian Pemberton, dorian@oakpartners.example

```html
<!DOCTYPE html>
<html lang="en">
<head>
<meta charset="utf-8">
<title>Oak Partners – Business Cards</title>
<link href="https://fonts.googleapis.com/css2?family=Michroma&family=Montserrat:wght@400;800&display=swap" rel="stylesheet">
<style>
  :root {
    --backdrop: #e3e8ea;
    --navy: #24316d;
    --navy-deep: #1f2b64;
    --sky: #3d93d8;
    --mid-blue: #3470c0;
    --white: #ffffff;
  }
  * { box-sizing: border-box; margin: 0; padding: 0; }
  html, body { width: 1200px; height: 960px; overflow: hidden; }
  body { background: var(--backdrop); position: relative; font-family: "Michroma", sans-serif; }

  .card {
    position: absolute;
    top: 105px;
    width: 430px;
    height: 750px;
    border-radius: 24px;
    overflow: hidden;
  }

  /* Front */
  .card--front { left: 143px; background: var(--navy-deep); }
  .front-pattern {
    position: absolute; inset: 0;
    background:
      linear-gradient(112deg, var(--sky) 0%, #3a87d0 28%, var(--mid-blue) 40%, #2a4a94 52%, var(--navy-deep) 64%, var(--navy-deep) 100%);
  }
  .front-mark {
    position: absolute;
    left: 179px; top: 495px;
    width: 70px; height: 70px;
    background: var(--white);
  }
  .front-brand {
    position: absolute;
    left: 165px;
    top: 471px;
    transform: rotate(-90deg);
    transform-origin: left top;
    color: var(--white);
    line-height: 1;
    white-space: nowrap;
  }
  .front-brand span { display: block; font-size: 36px; }
  .front-brand .brand-top { margin-bottom: 6px; }

  /* Back */
  .card--back { left: 631px; background: var(--white); color: var(--navy); }
  .back-mark {
    position: absolute;
    left: 90px; top: 48px;
    width: 52px; height: 52px;
    background: var(--navy);
  }
  .back-brand {
    position: absolute;
    left: 154px; top: 44px;
    line-height: 1.05;
    white-space: nowrap;
  }
  .back-brand span { display: block; font-size: 26px; }

  .person-name {
    position: absolute;
    left: 36px; top: 519px;
    font-family: "Montserrat", sans-serif;
    font-size: 30px;
    letter-spacing: 1px;
    white-space: nowrap;
  }
  .person-name .given { font-weight: 800; }
  .person-name .family { font-weight: 400; }

  .rule-v { position: absolute; left: 72px; top: 570px; bottom: 0; width: 2px; background: var(--navy); }
  .rule-h { position: absolute; left: 0; right: 0; height: 2px; background: var(--navy); }
  .contact-row {
    position: absolute; left: 0; right: 0; height: 43px;
    display: flex; align-items: center;
  }
  .contact-icon { width: 96px; display: flex; justify-content: center; padding-right: 0; position: absolute; left: 0; width: 72px; }
  .contact-icon svg { width: 20px; height: 20px; }
  .contact-text { position: absolute; left: 86px; white-space: nowrap; }
  .contact-text--phone { font-size: 15px; }
  .contact-text--web, .contact-text--mail { font-size: 12.5px; }
</style>
</head>
<body>

<section class="card card--front" aria-label="Card front">
  <div class="front-pattern" role="img" aria-label="Repeating pattern of small standing figures fading from light blue to navy"></div>
  <div class="front-mark" aria-hidden="true"></div>
  <div class="front-brand">
    <span class="brand-top">OAK</span>
    <span class="brand-bottom">PARTNERS</span>
  </div>
</section>

<section class="card card--back" aria-label="Card back">
  <div class="back-mark" aria-hidden="true"></div>
  <div class="back-brand">
    <span class="brand-top">OAK</span>
    <span class="brand-bottom">PARTNERS</span>
  </div>

  <h1 class="person-name"><span class="given">DORIAN</span> <span class="family">PEMBERTON</span></h1>

  <div class="rule-v"></div>
  <div class="rule-h" style="top:589px"></div>
  <div class="rule-h" style="top:634px"></div>
  <div class="rule-h" style="top:679px"></div>
  <div class="rule-h" style="top:724px"></div>

  <div class="contact-row" style="top:591px">
    <div class="contact-icon">
      <svg viewBox="0 0 24 24" fill="var(--navy)"><path d="M6.6 3.5l2.6 3.4-1.6 2.2c1 2.4 2.9 4.3 5.3 5.3l2.2-1.6 3.4 2.6-1.5 3.2C10.7 18.4 5.6 13.3 3.4 6.6z"/><path d="M14 3a7 7 0 017 7h-1.6A5.4 5.4 0 0014 4.6zM14 6.4a3.6 3.6 0 013.6 3.6H16a2 2 0 00-2-2z"/></svg>
    </div>
    <div class="contact-text contact-text--phone">800-555-0147</div>
  </div>

  <div class="contact-row" style="top:636px">
    <div class="contact-icon">
      <svg viewBox="0 0 24 24" fill="none" stroke="var(--navy)" stroke-width="2"><circle cx="12" cy="12" r="9"/><path d="M3 12h18M12 3c3 3 3 15 0 18M12 3c-3 3-3 15 0 18"/></svg>
    </div>
    <div class="contact-text contact-text--web">WWW.OAKPARTNERS.EXAMPLE</div>
  </div>

  <div class="contact-row" style="top:681px">
    <div class="contact-icon">
      <svg viewBox="0 0 24 24" fill="none" stroke="var(--navy)" stroke-width="1.8"><path d="M3 10l9-6 9 6v10H3z"/><path d="M3 10l9 6 9-6"/></svg>
    </div>
    <div class="contact-text contact-text--mail">DORIAN@OAKPARTNERS.EXAMPLE</div>
  </div>
</section>

</body>
</html>
```